Senior sex novelty store providing a private method for acquiring the products and knowledge

Our business supplies novelty sex products and services, specializing in the 50+ demographic. Products include sex products for individuals and couples. Services include webinars and teleseminars that address various sex and relationship issues. We are dedicated to providing discreet delivery of products and knowledge to people over 50 entering a new phase of life, facing new challenges. Our entire process from site through shipping is kept private to allow our customers the freedom to shop and learn in the privacy of their own home.

Target Market(s)

Seniors over 50 years old

Industry/Entity Type

Store

Number of Pages Required

1 page

Font styles to use
Serif

Requirements
Must have
• place for business description with a private look
Should not have
• anything sleazy

```html
<!DOCTYPE html>
<html lang="en">
<head>
<meta charset="utf-8">
<title>Quiet Hours — Discreet Wellness Store</title>
<link href="https://fonts.googleapis.com/css2?family=Lobster&family=Raleway:wght@400;500;600;700&family=Open+Sans:wght@400;600;700&display=swap" rel="stylesheet">
<style>
:root{
  --pink:#ec1b7a;
  --dark:#333333;
  --darker:#2b2b2b;
  --page:#f2f2f2;
  --white:#ffffff;
  --text:#555555;
  --muted:#8a8a8a;
  --line:#e2e2e2;
  --star:#f08a24;
  --stock:#5aa02c;
  --banner:#dcdad7;
}
*{box-sizing:border-box;margin:0;padding:0}
html,body{width:1200px;height:2535px;overflow:hidden}
body{background:var(--page);font-family:"Open Sans",sans-serif;color:var(--text);position:relative}
.wrap{position:absolute;left:108px;width:984px}

/* top bar */
.topbar{top:0;height:34px;display:flex;align-items:center;justify-content:space-between;font-size:11px;color:#666}
.topbar b{color:#222}
.topbar .links{display:flex;gap:24px;align-items:center}
.topbar svg{vertical-align:-2px;margin-right:6px}

/* header */
.header{top:34px;height:98px;display:flex;align-items:center;justify-content:space-between}
.brand{font-family:"Raleway",sans-serif;font-weight:700;font-size:44px;color:var(--pink);letter-spacing:-1px}
.tagline{font-family:"Raleway",sans-serif;font-style:italic;font-weight:600;font-size:13.5px;letter-spacing:.6px;color:#222}
.cart{width:232px;height:38px;background:var(--pink);color:var(--white);display:flex;align-items:center;padding:0 16px;font-family:"Raleway",sans-serif;font-size:15px;gap:10px}
.cart small{font-size:10px}
.cart .caret{margin-left:auto}

/* nav */
.nav{position:absolute;left:0;top:132px;width:1200px;height:47px;background:var(--dark)}
.nav .wrap{height:47px;display:flex;align-items:center}
.nav a{color:#eee;text-decoration:none;font-size:12px;text-transform:uppercase;padding:0 29px;height:47px;display:flex;align-items:center;border-right:1px solid #444;letter-spacing:.3px}
.nav a:first-child{padding-left:18px}
.search{margin-left:auto;width:230px;height:29px;background:var(--white);display:flex;align-items:center;justify-content:space-between;padding:0 10px;font-size:11px;color:#777}

/* hero */
.hero{position:absolute;left:0;top:179px;width:1200px;height:497px;background:linear-gradient(120deg,#e9e3dc 0%,#f7f4ef 40%,#d9cbbd 70%,#7a5a44 100%)}

/* about */
.about{top:704px;text-align:center}
.about h1{font-family:"Raleway",sans-serif;font-weight:400;font-size:31px;color:#222;letter-spacing:.5px}
.about h2{font-family:"Raleway",sans-serif;font-weight:600;font-size:15px;color:var(--pink);margin-top:6px;letter-spacing:.3px}
.about p{font-size:11.5px;line-height:16px;color:#666;margin-top:8px}
.services-title{top:826px;text-align:center;font-family:"Raleway",sans-serif;font-size:19px;color:#222}

/* services */
.service{position:absolute;top:862px;width:489px;height:160px;background:#dddcd9;border-bottom:2px solid #e6e6e6}
.service .photo{position:absolute;left:0;top:0;width:235px;height:160px}
.service .body{position:absolute;left:240px;top:18px}
.service h3{font-family:"Lobster",cursive;font-weight:400;font-size:41px;color:#2a2a2a}
.service p{font-size:11px;line-height:14px;color:#444;margin-top:4px;width:200px}
.btn{display:inline-block;background:var(--pink);color:var(--white);font-size:11px;text-transform:uppercase;padding:0 14px;height:30px;line-height:30px;margin-top:12px}

/* featured */
.featured-bar{top:1071px;height:33px;background:var(--white);display:flex;align-items:center;justify-content:space-between}
.featured-tag{height:33px;background:var(--pink);color:var(--white);font-family:"Lobster",cursive;font-size:20px;display:flex;align-items:center;padding:0 32px 0 14px;clip-path:polygon(0 0,100% 0,90% 50%,100% 100%,0 100%)}
.arrows{display:flex;gap:2px}
.arrows span{width:30px;height:33px;background:var(--pink);display:flex;align-items:center;justify-content:center}

.grid{display:grid;grid-template-columns:repeat(5,181px);column-gap:20px}
.card{height:313px;background:var(--white);position:relative;font-size:10.5px}
.card .thumb{margin:10px;height:130px}
.card h4{font-family:"Raleway",sans-serif;font-weight:500;font-size:13px;color:#222;margin:12px 10px 0}
.card .desc{margin:6px 10px 0;color:#888;line-height:15px}
.card .stars{margin:6px 10px 0;color:var(--star);font-size:12px;letter-spacing:1px}
.card .price{margin:4px 10px 0;color:var(--pink);font-size:15px}
.card .price s{color:#999;font-size:11px;margin-left:2px}
.card .stock{margin:2px 10px 0;color:var(--stock)}
.card .actions{position:absolute;left:0;bottom:0;width:100%;height:32px;display:flex;border-top:1px solid var(--line)}
.card .add{width:91px;background:var(--dark);color:var(--white);font-size:9px;display:flex;align-items:center;justify-content:center;gap:4px;text-transform:uppercase}
.card .icon{flex:1;display:flex;align-items:center;justify-content:center;border-left:1px solid var(--line)}
.t1{background:radial-gradient(circle,#c4303e 0%,#5b3a6e 45%,#fff 75%)}
.t2{background:radial-gradient(circle,#8c8c8c 0%,#3c3c3c 40%,#fff 72%)}
.t3{background:radial-gradient(circle,#e7d9cf 0%,#a01636 40%,#fff 72%)}
.t4{background:radial-gradient(ellipse,#e6c0a6 0%,#b796c9 40%,#fff 72%)}
.t5{background:radial-gradient(circle,#c98ae0 0%,#6a2aa6 40%,#fff 72%)}

/* sale banner */
.sale{top:1846px;height:170px;background:var(--banner);text-align:center;padding-top:28px}
.sale h3{font-family:"Lobster",cursive;font-weight:400;font-size:27px;color:#2a2a2a}
.sale p{font-size:13px;color:#444;margin-top:6px}
.sale .btn{margin-top:18px;height:34px;line-height:34px;padding:0 20px}

/* perks */
.perks{top:2079px;height:101px;display:flex}
.perk{flex:1;text-align:center;border-right:1px solid #d2d2d2}
.perk:last-child{border-right:0}
.perk h5{font-family:"Lobster",cursive;font-weight:400;font-size:25px;color:#2a2a2a;margin-top:6px}
.perk p{font-size:12px;color:#777;margin-top:2px}

/* footer */
.footer{position:absolute;left:0;top:2219px;width:1200px;height:316px;background:var(--darker);color:#999;font-size:11px}
.fcol{position:absolute;top:32px}
.fcol h6{font-family:"Raleway",sans-serif;font-weight:500;font-size:17px;color:var(--white);margin-bottom:10px}
.fcol li{list-style:none;line-height:24px}
.store li{display:flex;gap:10px;align-items:flex-start;line-height:20px;margin-bottom:10px}
.store .hl{color:var(--pink)}
.social{display:flex;gap:11px;margin-top:12px}
.social span{width:38px;height:38px;border-radius:50%;background:var(--pink)}
.bottom{position:absolute;left:101px;top:274px;width:1000px;border-top:1px solid #444;padding-top:10px;display:flex;justify-content:space-between;font-size:10.5px}
</style>
</head>
<body>

<div class="wrap topbar">
  <div><svg width="11" height="11" viewBox="0 0 24 24"><path fill="#555" d="M6.6 10.8a15 15 0 006.6 6.6l2.2-2.2c.3-.3.7-.4 1-.2 1.1.4 2.3.6 3.6.6.6 0 1 .4 1 1V20c0 .6-.4 1-1 1A17 17 0 013 4c0-.6.4-1 1-1h3.5c.6 0 1 .4 1 1 0 1.3.2 2.5.6 3.6.1.3 0 .7-.2 1z"/></svg>Call us now: <b>0100-555-012</b></div>
  <div class="links"><span>Contact us</span><span>English &#8964;</span><span>Currency: <b>USD</b> &#8964;</span><b>Sign in</b></div>
</div>

<header class="wrap header">
  <div class="brand">Quiet Hours</div>
  <div class="tagline">PRIVACY GUARANTEED · DISCREET SHIPPING · DISCREET BILLING</div>
  <div class="cart">
    <svg width="18" height="16" viewBox="0 0 24 22"><path fill="#fff" d="M0 1h4l1 4h19l-3 9H7L4 3H0zM8 18a2 2 0 110 4 2 2 0 010-4zm11 0a2 2 0 110 4 2 2 0 010-4z"/></svg>
    <span>Cart <small>(empty)</small></span><span class="caret">&#9662;</span>
  </div>
</header>

<nav class="nav"><div class="wrap" style="left:108px">
  <a>For Individual</a><a>For Couples</a><a>Best Sellers</a><a>Webinars</a><a>Teleseminars</a>
  <div class="search">SEARCH <svg width="13" height="13" viewBox="0 0 24 24"><circle cx="10" cy="10" r="7" fill="none" stroke="#222" stroke-width="3"/><path d="M15 15l7 7" stroke="#222" stroke-width="3"/></svg></div>
</div></nav>

<div class="hero" role="img" aria-label="Smiling mature couple sitting together on a bed in a bright bedroom"></div>

<section class="wrap about">
  <h1>ABOUT QUIET HOURS</h1>
  <h2>DUIS SED ODIO SIT AMET NIBH VULPUTATE CURSUS A SIT SOCIOSQU AD LITORA</h2>
  <p>Lorem ipsum dolor sit amet, consectetur adipiscing elit. Nulla mi eros, facilisis ac mollis et, ullamcorper non neque. Cum sociis natoque penatibus et magnis dis parturient<br>montes, nascetur ridiculus mus. Sed ac pretium dui. Praesent arcu dui, convallis eget facilisis in, vulputate ut lacus. Aliquam ultricies laoreet malesuada.</p>
</section>
<div class="wrap services-title">OUR SERVICES</div>

<div class="service" style="left:108px">
  <div class="photo" role="img" aria-label="Mature couple relaxing together on a sofa" style="background:linear-gradient(90deg,#e7b7c8,#f2ece8 60%,#dddcd9)"></div>
  <div class="body"><h3>Teleseminars</h3><p>Service that adddress various sex and relationship issues</p><span class="btn">Buy Now</span></div>
</div>
<div class="service" style="left:605px">
  <div class="photo" role="img" aria-label="Mature couple looking at a laptop together" style="background:linear-gradient(90deg,#f4f2ef,#cfc3b8 60%,#dddcd9)"></div>
  <div class="body"><h3>Webinars</h3><p>Service that adddress various sex and relationship issues</p><span class="btn">Buy Now</span></div>
</div>

<div class="wrap featured-bar">
  <div class="featured-tag">Featured</div>
  <div class="arrows">
    <span><svg width="8" height="10" viewBox="0 0 8 10"><path d="M6 1L2 5l4 4" stroke="#fff" stroke-width="2" fill="none"/></svg></span>
    <span><svg width="8" height="10" viewBox="0 0 8 10"><path d="M2 1l4 4-4 4" stroke="#fff" stroke-width="2" fill="none"/></svg></span>
  </div>
</div>

<div class="wrap grid" style="top:1132px;row-gap:37px">
  <div class="card"><div class="thumb t1" role="img" aria-label="Soft restraint with heart detail"></div><h4>Donec magna diam</h4><p class="desc">Lorem psum dolor aet cosctetur aipiscing elit nunc aiquet varius</p><div class="stars">★★★☆☆</div><div class="price">$200.00 <s>$250.00</s></div><div class="stock">In stock</div><div class="actions"><span class="add"><svg width="9" height="8" viewBox="0 0 24 22"><path fill="#fff" d="M0 1h4l1 4h19l-3 9H7L4 3H0z"/></svg>Add to cart</span><span class="icon"><svg width="10" height="9" viewBox="0 0 24 22"><path fill="#888" d="M12 21L2 11a6 6 0 0110-7 6 6 0 0110 7z"/></svg></span><span class="icon"><svg width="11" height="7" viewBox="0 0 24 14"><path fill="#888" d="M12 0C6 0 1 7 1 7s5 7 11 7 11-7 11-7S18 0 12 0zm0 11a4 4 0 110-8 4 4 0 010 8z"/></svg></span></div></div>
  <div class="card"><div class="thumb t2" role="img" aria-label="Compact silver massager"></div><h4>Donec magna diam</h4><p class="desc">Lorem psum dolor aet cosctetur aipiscing elit nunc aiquet varius</p><div class="stars">★★★☆☆</div><div class="price">$200.00 <s>$250.00</s></div><div class="stock">In stock</div><div class="actions"><span class="add"><svg width="9" height="8" viewBox="0 0 24 22"><path fill="#fff" d="M0 1h4l1 4h19l-3 9H7L4 3H0z"/></svg>Add to cart</span><span class="icon"><svg width="10" height="9" viewBox="0 0 24 22"><path fill="#888" d="M12 21L2 11a6 6 0 0110-7 6 6 0 0110 7z"/></svg></span><span class="icon"><svg width="11" height="7" viewBox="0 0 24 14"><path fill="#888" d="M12 0C6 0 1 7 1 7s5 7 11 7 11-7 11-7S18 0 12 0zm0 11a4 4 0 110-8 4 4 0 010 8z"/></svg></span></div></div>
  <div class="card"><div class="thumb t3" role="img" aria-label="Red satin glove with cream accessory"></div><h4>Donec magna diam</h4><p class="desc">Lorem psum dolor aet cosctetur aipiscing elit nunc aiquet varius</p><div class="stars">★★★☆☆</div><div class="price">$200.00 <s>$250.00</s></div><div class="stock">In stock</div><div class="actions"><span class="add"><svg width="9" height="8" viewBox="0 0 24 22"><path fill="#fff" d="M0 1h4l1 4h19l-3 9H7L4 3H0z"/></svg>Add to cart</span><span class="icon"><svg width="10" height="9" viewBox="0 0 24 22"><path fill="#888" d="M12 21L2 11a6 6 0 0110-7 6 6 0 0110 7z"/></svg></span><span class="icon"><svg width="11" height="7" viewBox="0 0 24 14"><path fill="#888" d="M12 0C6 0 1 7 1 7s5 7 11 7 11-7 11-7S18 0 12 0zm0 11a4 4 0 110-8 4 4 0 010 8z"/></svg></span></div></div>
  <div class="card"><div class="thumb t4" role="img" aria-label="Assorted accessory set"></div><h4>Donec magna diam</h4><p class="desc">Lorem psum dolor aet cosctetur aipiscing elit nunc aiquet varius</p><div class="stars">★★★☆☆</div><div class="price">$200.00 <s>$250.00</s></div><div class="stock">In stock</div><div class="actions"><span class="add"><svg width="9" height="8" viewBox="0 0 24 22"><path fill="#fff" d="M0 1h4l1 4h19l-3 9H7L4 3H0z"/></svg>Add to cart</span><span class="icon"><svg width="10" height="9" viewBox="0 0 24 22"><path fill="#888" d="M12 21L2 11a6 6 0 0110-7 6 6 0 0110 7z"/></svg></span><span class="icon"><svg width="11" height="7" viewBox="0 0 24 14"><path fill="#888" d="M12 0C6 0 1 7 1 7s5 7 11 7 11-7 11-7S18 0 12 0zm0 11a4 4 0 110-8 4 4 0 010 8z"/></svg></span></div></div>
  <div class="card"><div class="thumb t5" role="img" aria-label="Purple silicone set"></div><h4>Donec magna diam</h4><p class="desc">Lorem psum dolor aet cosctetur aipiscing elit nunc aiquet varius</p><div class="stars">★★★☆☆</div><div class="price">$200.00 <s>$250.00</s></div><div class="stock">In stock</div><div class="actions"><span class="add"><svg width="9" height="8" viewBox="0 0 24 22"><path fill="#fff" d="M0 1h4l1 4h19l-3 9H7L4 3H0z"/></svg>Add to cart</span><span class="icon"><svg width="10" height="9" viewBox="0 0 24 22"><path fill="#888" d="M12 21L2 11a6 6 0 0110-7 6 6 0 0110 7z"/></svg></span><span class="icon"><svg width="11" height="7" viewBox="0 0 24 14"><path fill="#888" d="M12 0C6 0 1 7 1 7s5 7 11 7 11-7 11-7S18 0 12 0zm0 11a4 4 0 110-8 4 4 0 010 8z"/></svg></span></div></div>

  <div class="card"><div class="thumb t1" role="img" aria-label="Soft restraint with heart detail"></div><h4>Donec magna diam</h4><p class="desc">Lorem psum dolor aet cosctetur aipiscing elit nunc aiquet varius</p><div class="stars">★★★☆☆</div><div class="price">$200.00 <s>$250.00</s></div><div class="stock">In stock</div><div class="actions"><span class="add"><svg width="9" height="8" viewBox="0 0 24 22"><path fill="#fff" d="M0 1h4l1 4h19l-3 9H7L4 3H0z"/></svg>Add to cart</span><span class="icon"><svg width="10" height="9" viewBox="0 0 24 22"><path fill="#888" d="M12 21L2 11a6 6 0 0110-7 6 6 0 0110 7z"/></svg></span><span class="icon"><svg width="11" height="7" viewBox="0 0 24 14"><path fill="#888" d="M12 0C6 0 1 7 1 7s5 7 11 7 11-7 11-7S18 0 12 0zm0 11a4 4 0 110-8 4 4 0 010 8z"/></svg></span></div></div>
  <div class="card"><div class="thumb t2" role="img" aria-label="Compact silver massager"></div><h4>Donec magna diam</h4><p class="desc">Lorem psum dolor aet cosctetur aipiscing elit nunc aiquet varius</p><div class="stars">★★★☆☆</div><div class="price">$200.00 <s>$250.00</s></div><div class="stock">In stock</div><div class="actions"><span class="add"><svg width="9" height="8" viewBox="0 0 24 22"><path fill="#fff" d="M0 1h4l1 4h19l-3 9H7L4 3H0z"/></svg>Add to cart</span><span class="icon"><svg width="10" height="9" viewBox="0 0 24 22"><path fill="#888" d="M12 21L2 11a6 6 0 0110-7 6 6 0 0110 7z"/></svg></span><span class="icon"><svg width="11" height="7" viewBox="0 0 24 14"><path fill="#888" d="M12 0C6 0 1 7 1 7s5 7 11 7 11-7 11-7S18 0 12 0zm0 11a4 4 0 110-8 4 4 0 010 8z"/></svg></span></div></div>
  <div class="card"><div class="thumb t3" role="img" aria-label="Red satin glove with cream accessory"></div><h4>Donec magna diam</h4><p class="desc">Lorem psum dolor aet cosctetur aipiscing elit nunc aiquet varius</p><div class="stars">★★★☆☆</div><div class="price">$200.00 <s>$250.00</s></div><div class="stock">In stock</div><div class="actions"><span class="add"><svg width="9" height="8" viewBox="0 0 24 22"><path fill="#fff" d="M0 1h4l1 4h19l-3 9H7L4 3H0z"/></svg>Add to cart</span><span class="icon"><svg width="10" height="9" viewBox="0 0 24 22"><path fill="#888" d="M12 21L2 11a6 6 0 0110-7 6 6 0 0110 7z"/></svg></span><span class="icon"><svg width="11" height="7" viewBox="0 0 24 14"><path fill="#888" d="M12 0C6 0 1 7 1 7s5 7 11 7 11-7 11-7S18 0 12 0zm0 11a4 4 0 110-8 4 4 0 010 8z"/></svg></span></div></div>
  <div class="card"><div class="thumb t4" role="img" aria-label="Assorted accessory set"></div><h4>Donec magna diam</h4><p class="desc">Lorem psum dolor aet cosctetur aipiscing elit nunc aiquet varius</p><div class="stars">★★★☆☆</div><div class="price">$200.00 <s>$250.00</s></div><div class="stock">In stock</div><div class="actions"><span class="add"><svg width="9" height="8" viewBox="0 0 24 22"><path fill="#fff" d="M0 1h4l1 4h19l-3 9H7L4 3H0z"/></svg>Add to cart</span><span class="icon"><svg width="10" height="9" viewBox="0 0 24 22"><path fill="#888" d="M12 21L2 11a6 6 0 0110-7 6 6 0 0110 7z"/></svg></span><span class="icon"><svg width="11" height="7" viewBox="0 0 24 14"><path fill="#888" d="M12 0C6 0 1 7 1 7s5 7 11 7 11-7 11-7S18 0 12 0zm0 11a4 4 0 110-8 4 4 0 010 8z"/></svg></span></div></div>
  <div class="card"><div class="thumb t5" role="img" aria-label="Purple silicone set"></div><h4>Donec magna diam</h4><p class="desc">Lorem psum dolor aet cosctetur aipiscing elit nunc aiquet varius</p><div class="stars">★★★☆☆</div><div class="price">$200.00 <s>$250.00</s></div><div class="stock">In stock</div><div class="actions"><span class="add"><svg width="9" height="8" viewBox="0 0 24 22"><path fill="#fff" d="M0 1h4l1 4h19l-3 9H7L4 3H0z"/></svg>Add to cart</span><span class="icon"><svg width="10" height="9" viewBox="0 0 24 22"><path fill="#888" d="M12 21L2 11a6 6 0 0110-7 6 6 0 0110 7z"/></svg></span><span class="icon"><svg width="11" height="7" viewBox="0 0 24 14"><path fill="#888" d="M12 0C6 0 1 7 1 7s5 7 11 7 11-7 11-7S18 0 12 0zm0 11a4 4 0 110-8 4 4 0 010 8z"/></svg></span></div></div>
</div>

<section class="wrap sale">
  <h3>Save Friday Sale - Discounts up to 70%</h3>
  <p>Lorem Ipsum is simply dummy text of the printing and typesetting industry.</p>
  <span class="btn">Shop Now</span>
</section>

<section class="wrap perks">
  <div class="perk">
    <svg width="30" height="28" viewBox="0 0 24 22"><path fill="#ec1b7a" d="M1 9h4v12H1zM7 20V9l5-8c2 0 3 1 2 4l-1 3h7c2 0 3 2 2 4l-2 7c-1 1-1 1-2 1z"/></svg>
    <h5>Free Shipping</h5><p>On Orders Over $99</p>
  </div>
  <div class="perk">
    <svg width="30" height="28" viewBox="0 0 24 22"><rect x="1" y="4" width="22" height="16" rx="2" fill="#ec1b7a"/><rect x="4" y="1" width="5" height="6" fill="#ec1b7a"/><g fill="#fff"><rect x="11" y="8" width="2" height="2"/><rect x="15" y="8" width="2" height="2"/><rect x="19" y="8" width="2" height="2"/><rect x="11" y="12" width="2" height="2"/><rect x="15" y="12" width="2" height="2"/><rect x="19" y="12" width="2" height="2"/><rect x="4" y="9" width="4" height="8"/></g></svg>
    <h5>+010 55 501 234</h5><p>Contact Our Support 24/7</p>
  </div>
  <div class="perk">
    <svg width="32" height="28" viewBox="0 0 26 22"><ellipse cx="13" cy="12" rx="10" ry="8" fill="#ec1b7a"/><rect x="7" y="17" width="3" height="5" fill="#ec1b7a"/><rect x="16" y="17" width="3" height="5" fill="#ec1b7a"/><circle cx="13" cy="3" r="3" fill="#ec1b7a"/></svg>
    <h5>Discount System</h5><p>Refferal Bonus and Reward</p>
  </div>
</section>

<footer class="footer">
  <div class="fcol" style="left:101px"><h6>Categories</h6><ul><li>Indivdual</li><li>Couples</li><li>Best Sellers</li><li>Webinars</li><li>Teleseminars</li></ul></div>
  <div class="fcol" style="left:272px"><h6>Information</h6><ul><li>Specials</li><li>New products</li><li>Best sellers</li><li>Our stores</li><li>Contact us</li><li>Terms and conditions of use</li><li>About us</li><li>Sitemap</li></ul></div>
  <div class="fcol" style="left:443px"><h6>My account</h6><ul><li>My orders</li><li>My credit slips</li><li>My addresses</li><li>My personal info</li></ul></div>
  <div class="fcol store" style="left:791px;width:310px"><h6>Store Information</h6><ul>
    <li><svg width="14" height="18" viewBox="0 0 14 20"><path fill="#777" d="M7 0a7 7 0 017 7c0 5-7 13-7 13S0 12 0 7a7 7 0 017-7zm0 4a3 3 0 100 6 3 3 0 000-6z"/></svg><span>Quiet Hours Co., 18 Linden Row 40210<br>Harbor City</span></li>
    <li><svg width="14" height="14" viewBox="0 0 24 24"><path fill="#777" d="M6.6 10.8a15 15 0 006.6 6.6l2.2-2.2c.3-.3.7-.4 1-.2 1.1.4 2.3.6 3.6.6.6 0 1 .4 1 1V20c0 .6-.4 1-1 1A17 17 0 013 4c0-.6.4-1 1-1h3.5c.6 0 1 .4 1 1 0 1.3.2 2.5.6 3.6.1.3 0 .7-.2 1z"/></svg><span>Call us now: <span class="hl">0100-555-0126</span></span></li>
    <li><svg width="16" height="12" viewBox="0 0 24 18"><rect x="1" y="1" width="22" height="16" fill="none" stroke="#777" stroke-width="2"/><path d="M1 1l11 9 11-9" fill="none" stroke="#777" stroke-width="2"/></svg><span>Email: <span class="hl">hello@quiethours.example</span></span></li>
  </ul>
  <div class="social"><span></span><span></span><span></span><span></span><span></span></div></div>
  <div class="bottom"><span>© 2015 Quiet Hours LLC. All Rights Reserved</span><span>Terms of Use &nbsp;|&nbsp; Privacy Policy</span></div>
</footer>

</body>
</html>
```